Coffee Bag Design for Tollbury Coffee

We’re excited to invite you to help us bring Tollbury Coffee to life on grocery store shelves with a design that embodies our mission of spreading goodness and creating a lasting impact. Tollbury Coffee represents warmth, positivity, and the power of small actions to create ripples of goodness. Each cup not only offers a rich, gourmet coffee experience but also gives back to the community, with $2 from each bag supporting local food banks.

To reflect this vision, we’d love for the design to feature a dark (greyish) blue as the base color to convey depth and quality, complemented by a vibrant light blue that will catch the eye and add energy. Tan or gold accents could add an elegant touch and a feeling of warmth. We are aiming for a look that feels uplifting and engaging, with simplicity and elegance, yet stands out amid other brands on the shelf.

I am attaching the dimension of the bag.

Other information that needs to be listed:
Ingredients: 100% Arabica Coffee
Net Wt. 12 oz. (340 g)
Roasted and distributed by:
Name
Address
email

Text on the back of the bag:
Tollbury Coffee is crafted with a belief that kindness and positivity can spread, touching countless lives with every sip. This gourmet blend delivers a rich taste experience while giving back, as $2 from each bag sold is donated to local food banks to help those in need. Enjoy the warmth and goodness in each cup, knowing you’re making a difference with every purchase.

Thank you!

```html
<!DOCTYPE html>
<html lang="en">
<head>
<meta charset="utf-8">
<title>Tollbury Coffee – Bag Dieline</title>
<link rel="stylesheet" href="https://fonts.googleapis.com/css2?family=Fira+Sans+Condensed:wght@700&family=Fira+Sans:wght@400;600&family=Jost:wght@400;600&display=swap">
<style>
  :root {
    --stage: #5e5e5e;
    --slate: #3d6080;
    --slate-deep: #2f506a;
    --aqua: #9fd8dc;
    --mist: #e9f3f4;
    --teal: #5fb6c4;
    --gold: #b07a2a;
    --gold-light: #e0b85a;
    --white: #ffffff;
    --ink: #1b2a36;
    --zip: rgba(190, 130, 210, 0.45);
  }
  * { box-sizing: border-box; margin: 0; padding: 0; }
  html, body { width: 990px; height: 1200px; overflow: hidden; }
  body { background: var(--stage); position: relative; font-family: "Fira Sans", sans-serif; }

  .dieline { position: absolute; left: 29px; top: 336px; width: 932px; height: 528px; }

  .panel { position: absolute; top: 0; height: 364px; border-radius: 8px; overflow: hidden; }
  .panel--side { background: var(--slate); width: 161px; }
  .panel--side-left { left: 0; }
  .panel--side-right { left: 467px; }
  .panel--front { left: 162px; width: 304px; }
  .panel--back { left: 628px; width: 304px; }
  .panel--bottom { left: 162px; top: 365px; width: 304px; height: 163px; background: var(--slate); }

  .marble {
    position: absolute; inset: 0;
    background:
      radial-gradient(ellipse at 60% 30%, var(--mist) 0%, rgba(233,243,244,0) 45%),
      radial-gradient(ellipse at 20% 80%, var(--teal) 0%, rgba(95,182,196,0) 55%),
      radial-gradient(ellipse at 85% 75%, #7cc6cf 0%, rgba(124,198,207,0) 50%),
      linear-gradient(160deg, #6fbdc8 0%, #bfe3e6 45%, #5aaab9 100%);
  }

  .front-strip { position: absolute; left: 0; top: 0; width: 115px; height: 100%; background: var(--slate); }
  .gold-rule { position: absolute; left: 115px; top: 0; width: 6px; height: 100%;
    background: linear-gradient(180deg, var(--gold), var(--gold-light) 50%, var(--gold)); }
  .front-marble { position: absolute; left: 121px; top: 0; right: 0; bottom: 0; }

  .brand-name {
    position: absolute; top: 50%; left: 50%;
    transform: translate(-50%, -50%) rotate(90deg);
    font-family: "Fira Sans Condensed", sans-serif; font-weight: 700;
    white-space: nowrap; letter-spacing: 1px; text-transform: uppercase;
  }
  .brand-name--front { left: 57px; font-size: 44px; color: var(--aqua); }
  .brand-name--side { font-size: 36px; color: var(--white); }

  .spec-label {
    position: absolute; left: 131px; top: 137px; width: 153px; height: 160px;
    background: var(--slate); color: var(--white); text-align: center;
    padding: 10px 8px; font-size: 9px; letter-spacing: 1px;
  }
  .spec-label .spec-title { font-weight: 600; }
  .spec-row { padding: 4px 0; border-bottom: 1px dashed rgba(255,255,255,0.75); }
  .spec-row--split { display: flex; }
  .spec-row--split > div { flex: 1; }
  .spec-row--split > div:first-child { border-right: 1px solid var(--white); text-align: left; }
  .spec-row--split > div:last-child { text-align: right; }
  .spec-weight { padding-top: 10px; font-family: "Fira Sans Condensed", sans-serif; font-weight: 700; letter-spacing: 0; font-size: 9.5px; }

  .zip-band { position: absolute; left: 18px; right: 0; top: 49px; height: 42px;
    background: linear-gradient(180deg, var(--zip), rgba(190,130,210,0.25)); }
  .zip-band::before { content: ""; position: absolute; left: 0; right: 0; top: 12px; height: 2px; background: #a04fb8; }

  .squeeze { position: absolute; left: 124px; top: 133px; width: 60px; height: 56px; }

  .mission {
    position: absolute; left: 20px; top: 193px; width: 264px; height: 129px;
    background: rgba(47, 80, 106, 0.88); border: 2px solid var(--gold); border-radius: 8px;
    color: var(--white); font-family: "Jost", sans-serif; font-size: 8.4px; line-height: 1.95;
    text-align: justify; text-align-last: center; padding: 7px 10px;
  }
</style>
</head>
<body>
  <main class="dieline">
    <section class="panel panel--side panel--side-left">
      <div class="brand-name brand-name--side">Tollbury Coffee</div>
    </section>

    <section class="panel panel--front">
      <div class="front-marble"><div class="marble" role="img" aria-label="Aqua and white watercolour marble pattern with gold veins"></div></div>
      <div class="front-strip"></div>
      <div class="gold-rule"></div>
      <div class="brand-name brand-name--front">Tollbury Coffee</div>
      <div class="spec-label">
        <div class="spec-row"><div class="spec-title">Flavor</div><div>Medium Roast</div></div>
        <div class="spec-row spec-row--split">
          <div><div class="spec-title">Process</div><div>National</div></div>
          <div><div class="spec-title">Date:</div><div>National</div></div>
        </div>
        <div class="spec-row"><div class="spec-title">Ingredients:</div><div>100%Arabica Coffee</div></div>
        <div class="spec-weight">Net Wt. 12 oz. (340 g)</div>
      </div>
    </section>

    <section class="panel panel--side panel--side-right">
      <div class="brand-name brand-name--side">Tollbury Coffee</div>
    </section>

    <section class="panel panel--back">
      <div class="marble" role="img" aria-label="Aqua and white watercolour marble pattern with gold veins"></div>
      <div class="zip-band"></div>
      <svg class="squeeze" viewBox="0 0 60 56" aria-label="Squeeze Me To Smell">
        <defs><path id="squeeze-arc" d="M6 30 A24 24 0 0 1 54 30"/></defs>
        <circle cx="30" cy="34" r="20" fill="none" stroke="#2f506a" stroke-width="0.8"/>
        <text font-family="Jost, sans-serif" font-size="6" font-weight="600" fill="#1b2a36">
          <textPath href="#squeeze-arc">Squeeze Me To Smell</textPath>
        </text>
      </svg>
      <p class="mission">Tollbury Coffee is crafted with the belief that kindness and positivity can spread, touching countless lives with every sip. This gourmet blend delivers a rich taste experience while giving back, as $2 from each bag sold is donated to local food banks to help those in need. Enjoy the warmth and goodness in each cup, knowing you’re making a difference with every purchase.</p>
    </section>

    <section class="panel panel--bottom"></section>
  </main>
</body>
</html>
```